QVR business card

Need a business card for a company that provides instructional design and elearning development services. The website is here: http://quorvane.studio/

I'm attaching a current logo, as well as the old business card design. While I like to keep it clean, the old design is too simplistic for my liking. The only idea I want to reuse from the old design is placing industry jargon on the back of the card, just need a better way to present it. But if you have other ideas for the back--feel free to experiment.

Please use the colors complementary to the color we have on the website. Thank you!

```html
<!DOCTYPE html>
<html lang="en">
<head>
<meta charset="utf-8">
<title>QVR business card</title>
<link href="https://fonts.googleapis.com/css2?family=Open+Sans:wght@400;600;700&display=swap" rel="stylesheet">
<style>
  :root {
    --stage: #2c2e32;
    --paper: #ffffff;
    --ink: #1d1d1d;
    --teal: #0fb0ad;
    --sand: #ddd293;
    --white: #ffffff;
    --mark-faint: rgba(120, 190, 170, 0.35);
  }
  * { box-sizing: border-box; margin: 0; padding: 0; }
  html, body {
    width: 1200px; height: 864px; overflow: hidden;
    background: var(--stage);
    font-family: "Open Sans", Arial, sans-serif;
  }
  .stage {
    position: relative; width: 1200px; height: 864px;
  }
  .card {
    position: absolute; left: 320px; width: 560px; height: 320px;
    border-radius: 4px; overflow: hidden;
    box-shadow: 0 14px 30px rgba(0,0,0,0.45);
  }
  .card--front { top: 72px; background: var(--paper); }
  .card--back {
    top: 472px;
    background: linear-gradient(180deg, var(--teal) 0%, #5cc1a8 45%, var(--sand) 100%);
  }

  /* front */
  .brand {
    position: absolute; top: 44px; left: 0; right: 0;
    display: flex; justify-content: center; align-items: center; gap: 14px;
  }
  .brand__dot {
    width: 26px; height: 26px; border-radius: 50%; background: var(--teal);
  }
  .brand__name {
    font-size: 52px; font-weight: 700; color: var(--teal); letter-spacing: 2px; line-height: 1;
  }
  .services__title {
    position: absolute; top: 140px; left: 0; right: 0; text-align: center;
    font-size: 15px; font-weight: 600; color: var(--teal); letter-spacing: 1px;
  }
  .services {
    position: absolute; top: 172px; left: 40px; right: 40px;
    display: grid; grid-template-columns: 1fr 14px 1fr; row-gap: 12px; column-gap: 12px;
    list-style: none; font-size: 14.5px; font-weight: 600; color: var(--ink);
  }
  .services__left { text-align: right; }
  .services__right { text-align: left; }
  .services__bullet {
    width: 8px; height: 8px; border-radius: 50%; background: var(--teal);
    align-self: center; justify-self: center;
  }

  /* back */
  .back__mark {
    position: absolute; left: 0; right: 0; top: 150px; text-align: center;
    font-size: 150px; font-weight: 700; color: var(--mark-faint); letter-spacing: 10px; line-height: 1;
  }
  .contact {
    position: absolute; top: 88px; left: 0; right: 0; text-align: center; color: var(--white);
  }
  .contact__name { font-size: 20px; font-weight: 700; margin-bottom: 34px; }
  .contact__line { font-size: 17px; font-weight: 400; line-height: 1.3; }
  .contact__label { font-weight: 700; }
</style>
</head>
<body>
<main class="stage">
  <section class="card card--front">
    <div class="brand">
      <span class="brand__dot"></span>
      <span class="brand__name">QVR</span>
    </div>
    <h2 class="services__title">HOW CAN WE HELP?</h2>
    <ul class="services">
      <li class="services__left">Mobile Learning Scorm</li>
      <li class="services__bullet"></li>
      <li class="services__right">Instructional Design Lms</li>
      <li class="services__left">Moocs Elearning Html5</li>
      <li class="services__bullet"></li>
      <li class="services__right">Adult Learning Theory</li>
      <li class="services__left">Gamification Classroom</li>
      <li class="services__bullet"></li>
      <li class="services__right">Xapi Blended Learning</li>
    </ul>
  </section>

  <section class="card card--back">
    <div class="back__mark" aria-hidden="true">QVR</div>
    <div class="contact">
      <p class="contact__name">Marcus Ellery</p>
      <p class="contact__line"><span class="contact__label">Phone:</span> 555-014-2286</p>
      <p class="contact__line"><span class="contact__label">Email:</span> mellery@quorvane.studio</p>
      <p class="contact__line"><span class="contact__label">Website:</span> www.quorvane.studio</p>
    </div>
  </section>
</main>
</body>
</html>
```